Business Card Re-Design/Update

We'd like to update out business cards. I've included our current "Style guide" which has the colour scheme of the organisation in it. I've also included the branding files with logos etc in them.

I've also included a copy of one of our existing cards so that you can see how ugly/dated they look. I'd like a fresh modern corporate look.

Target Market(s)

These are for our clients, potential clients, industry contacts - like all business cards

Contact Information for Business Card

Name
Position
Company Address - Level 1, 47 Fernby Street, Carlow Qld 4072
Direct Phone
mobile
Email
Website -www.korvalit.com.au
Logo

Colors

Designer to choose colors to be used in the design.

Requirements
Must have
• Main Logo
• Cards will need to be editable to be able to personalize them for each new employee.
Nice to have
• The MapOut, ShipWell, KeepSteady would be okay to have if they can be sensibly and professionally added to the look without detracting from the main imagery.
• Maybe they could go on the back of the card? will leave this to your creative discretion as to whether/where they fit.
Should not have
• Should not have decorative or script fonts

```html
<!DOCTYPE html>
<html lang="en">
<head>
<meta charset="utf-8">
<title>Korvalit Business Card</title>
<link rel="stylesheet" href="https://fonts.googleapis.com/css2?family=Roboto:ital,wght@0,400;0,500;0,700;1,400;1,500&display=swap">
<style>
  :root {
    --stage: #3a3431;
    --card: #1f2022;
    --red: #d0202e;
    --white: #f2f2f2;
    --green: #5f9a3a;
    --blue: #2f82c0;
    --magenta: #a4317f;
  }
  * { margin: 0; padding: 0; box-sizing: border-box; }
  html, body { width: 1200px; height: 769px; overflow: hidden; }
  body {
    background: var(--stage);
    font-family: "Roboto", Arial, sans-serif;
    position: relative;
  }
  .card {
    position: absolute;
    top: 230px;
    width: 540px;
    height: 309px;
    background: var(--card);
    border-radius: 3px;
    box-shadow: 0 14px 30px rgba(0,0,0,.45);
    overflow: hidden;
  }
  .card-back { left: 30px; }
  .card-front { left: 630px; }

  /* back */
  .back-brand {
    position: absolute; top: 72px; left: 0; right: 0;
    display: flex; align-items: center; justify-content: center; gap: 14px;
    color: var(--red); font-weight: 700; font-size: 46px; letter-spacing: .5px;
  }
  .back-brand .mark { width: 38px; height: 38px; background: var(--red); }
  .services {
    position: absolute; bottom: 62px; left: 0; right: 0;
    display: flex; justify-content: center; gap: 38px;
  }
  .service { display: flex; align-items: center; gap: 7px; font-size: 22px; font-weight: 500; }
  .service .dot { width: 14px; height: 14px; }
  .service-map { color: var(--green); } .service-map .dot { background: var(--green); }
  .service-ship { color: var(--blue); } .service-ship .dot { background: var(--blue); }
  .service-keep { color: var(--magenta); } .service-keep .dot { background: var(--magenta); }

  /* front */
  .front-brand {
    position: absolute; top: 44px; right: 38px;
    display: flex; align-items: center; gap: 10px;
    color: var(--white); font-weight: 700; font-size: 30px;
  }
  .front-brand .mark { width: 26px; height: 26px; background: var(--red); }
  .person { position: absolute; top: 52px; left: 34px; }
  .person-name { color: var(--red); font-size: 19px; font-weight: 500; text-transform: uppercase; letter-spacing: .3px; }
  .person-role { color: var(--white); font-size: 13px; margin-top: 2px; }
  .rule { position: absolute; top: 106px; left: 34px; right: 38px; height: 1.5px; background: var(--red); }
  .contacts { position: absolute; top: 124px; left: 34px; list-style: none; }
  .contacts li {
    display: flex; align-items: center; gap: 9px;
    color: var(--white); font-size: 13.5px; line-height: 20px;
  }
  .contacts svg { width: 12px; height: 12px; fill: var(--red); flex: none; }
  .address {
    position: absolute; bottom: 30px; right: 38px; text-align: right;
    color: var(--white); font-size: 13.5px; line-height: 19px;
  }
</style>
</head>
<body>

<section class="card card-back">
  <div class="back-brand"><span class="mark"></span>korvalit</div>
  <div class="services">
    <div class="service service-map"><span class="dot"></span>MapOut</div>
    <div class="service service-ship"><span class="dot"></span>ShipWell</div>
    <div class="service service-keep"><span class="dot"></span>KeepSteady</div>
  </div>
</section>

<section class="card card-front">
  <div class="person">
    <div class="person-name">Maren Holt</div>
    <div class="person-role">Business Development Manager</div>
  </div>
  <div class="front-brand"><span class="mark"></span>korvalit</div>
  <div class="rule"></div>
  <ul class="contacts">
    <li><svg viewBox="0 0 24 24"><path d="M6.6 10.8a15 15 0 0 0 6.6 6.6l2.2-2.2a1 1 0 0 1 1-.25 11.4 11.4 0 0 0 3.6.57 1 1 0 0 1 1 1V20a1 1 0 0 1-1 1A17 17 0 0 1 3 4a1 1 0 0 1 1-1h3.5a1 1 0 0 1 1 1c0 1.25.2 2.45.57 3.57a1 1 0 0 1-.25 1z"/></svg>+61 (0)7 3390 4120</li>
    <li><svg viewBox="0 0 24 24"><path d="M6.6 10.8a15 15 0 0 0 6.6 6.6l2.2-2.2a1 1 0 0 1 1-.25 11.4 11.4 0 0 0 3.6.57 1 1 0 0 1 1 1V20a1 1 0 0 1-1 1A17 17 0 0 1 3 4a1 1 0 0 1 1-1h3.5a1 1 0 0 1 1 1c0 1.25.2 2.45.57 3.57a1 1 0 0 1-.25 1z"/></svg>+61 (0)7 3390 4127</li>
    <li><svg viewBox="0 0 24 24"><path d="M7 1h10a2 2 0 0 1 2 2v18a2 2 0 0 1-2 2H7a2 2 0 0 1-2-2V3a2 2 0 0 1 2-2zm0 3v14h10V4z"/></svg>+61 (0)412 605 318</li>
    <li><svg viewBox="0 0 24 24"><path d="M6 2h12v6H6zM3 9h18a1 1 0 0 1 1 1v8h-4v4H6v-4H2v-8a1 1 0 0 1 1-1zm5 7v4h8v-4z"/></svg>+61 (0)7 3390 4199</li>
    <li><svg viewBox="0 0 24 24"><path d="M2 5h20v14H2zm2 2v.5l8 5 8-5V7z"/></svg>mholt@korvalit.com.au</li>
  </ul>
  <div class="address">
    Level 1, 47 Fernby Street<br>
    Carlow Qld 4072<br>
    www.korvalit.com.au
  </div>
</section>

</body>
</html>
```